Business card design Needed for new logo / Construction business, home extensions and new builds

We need a business card design using our new logo files which i will attach to this project :)

We are a small construction business specialising in home extensions, new builds and property development. We are very ambitious and would appreciate professional and elegant designs for our new business card.

Very serious about using the services on MakerQuarry and recently acquired our new logo from here :)

Please get involved, i will feedback when i can as i am very busy but can respond daily, thanks

Target Market(s)

People that want to build onto their houses, new building developments or adding too their existing property

Industry/Entity Type

Construction

Contact Information for Business Card

Renwick Tolliver Construction, Lionel Ashby (Managing Director), Tel 07822254961, email - info@renwick-tolliver, www.renwick-tolliver.co.uk

Colors

Designer to choose colors to be used in the design.

Requirements
Must have
• I like a deep grey on the back please. A lot of you have provided black from and back, try mixing things up a little. The black looks cool 😎 Thanks

```html
<!DOCTYPE html>
<html lang="en">
<head>
<meta charset="utf-8">
<title>Renwick Tolliver Construction – Business Card</title>
<link rel="stylesheet" href="https://fonts.googleapis.com/css2?family=Lato:wght@400;700&display=swap">
<style>
  :root {
    --backdrop: #161616;
    --card-edge: #000000;
    --card-glow: #232323;
    --back-grey: #3a3b3d;
    --back-grey-edge: #2a2b2d;
    --gold: #d99a1e;
    --gold-deep: #c8891a;
    --text-light: #f1f1f1;
    --text-muted: #b9b9b9;
    --band-text: #1a1208;
  }
  * { box-sizing: border-box; margin: 0; padding: 0; }
  html, body {
    width: 1200px; height: 1200px; overflow: hidden;
    background: var(--backdrop);
    font-family: "Lato", Arial, sans-serif;
  }
  .card {
    position: absolute; left: 250px; width: 700px; height: 400px;
    border-radius: 20px; overflow: hidden;
  }
  .card-front {
    top: 170px;
    background: radial-gradient(ellipse at 55% 50%, var(--card-glow) 0%, #0c0c0c 55%, var(--card-edge) 100%);
  }
  .card-back {
    top: 630px;
    background: radial-gradient(ellipse at 50% 50%, var(--back-grey) 0%, var(--back-grey-edge) 100%);
  }

  .brand-mark {
    position: absolute; left: 470px; top: 60px; width: 200px;
    text-align: center; color: var(--gold);
    font-weight: 700; font-size: 22px; line-height: 1.25; letter-spacing: 1px;
  }
  .brand-square {
    display: block; width: 22px; height: 22px; margin: 0 auto 12px;
    background: var(--gold);
  }

  .holder-name {
    position: absolute; left: 48px; top: 186px;
    color: var(--gold); font-weight: 700; font-size: 30px; letter-spacing: 0.2px;
  }
  .holder-role {
    position: absolute; left: 48px; top: 226px;
    color: var(--text-muted); font-size: 20px; font-weight: 400;
  }
  .divider {
    position: absolute; left: 49px; top: 267px; width: 603px; height: 1.5px;
    background: var(--gold-deep);
  }
  .contact {
    position: absolute; left: 48px; top: 286px; list-style: none;
    color: var(--text-light);
  }
  .contact li { display: flex; align-items: center; height: 26px; }
  .contact .phone { font-size: 20px; }
  .contact .email { font-size: 17px; }
  .contact svg { width: 16px; height: 16px; margin-right: 11px; fill: var(--gold); }
  .company-block {
    position: absolute; right: 48px; top: 288px; text-align: right;
  }
  .company-name { color: var(--gold); font-weight: 700; font-size: 17px; height: 26px; }
  .company-address { color: var(--text-light); font-size: 17px; }

  .web-band { position: absolute; left: 0; top: 365px; width: 700px; height: 35px; }
  .web-address {
    position: absolute; left: 0; top: 365px; width: 655px; height: 35px;
    display: flex; align-items: center; justify-content: center;
    color: var(--band-text); font-size: 17px; letter-spacing: 2.5px;
  }
  .web-address b { font-weight: 700; }

  .back-brand {
    position: absolute; left: 0; top: 110px; width: 700px; text-align: center;
    color: var(--gold); font-weight: 700; font-size: 40px; line-height: 1.3; letter-spacing: 2px;
  }
  .back-brand .brand-square { width: 34px; height: 34px; margin-bottom: 24px; }
</style>
</head>
<body>
  <section class="card card-front">
    <div class="brand-mark"><span class="brand-square"></span>RENWICK<br>TOLLIVER</div>

    <h1 class="holder-name">LIONEL ASHBY</h1>
    <p class="holder-role">Managing Director</p>
    <div class="divider"></div>

    <ul class="contact">
      <li class="phone">
        <svg viewBox="0 0 24 24" aria-hidden="true"><path d="M6.6 10.8a15.1 15.1 0 0 0 6.6 6.6l2.2-2.2a1 1 0 0 1 1-.25 11.4 11.4 0 0 0 3.6.57 1 1 0 0 1 1 1V20a1 1 0 0 1-1 1A17 17 0 0 1 3 4a1 1 0 0 1 1-1h3.5a1 1 0 0 1 1 1c0 1.25.2 2.45.57 3.57a1 1 0 0 1-.25 1z"/></svg>
        07822254961
      </li>
      <li class="email">
        <svg viewBox="0 0 24 24" aria-hidden="true"><path d="M2 5h20v14H2z M3.5 6.5 12 13l8.5-6.5v11h-17z" fill-rule="evenodd"/></svg>
        info@renwick-tolliver.co.uk
      </li>
    </ul>

    <div class="company-block">
      <p class="company-name">Renwick Tolliver Construction</p>
      <p class="company-address">Your Address, City, State, Zip 1235</p>
    </div>

    <svg class="web-band" viewBox="0 0 700 35" preserveAspectRatio="none" aria-hidden="true">
      <defs>
        <linearGradient id="band-gold" x1="0" x2="1" y1="0" y2="0">
          <stop offset="0" stop-color="#d38f12"/>
          <stop offset="0.5" stop-color="#ffd98a"/>
          <stop offset="1" stop-color="#d99a1e"/>
        </linearGradient>
        <linearGradient id="band-silver" x1="0" x2="1" y1="0" y2="0">
          <stop offset="0" stop-color="#e4e6e8"/>
          <stop offset="1" stop-color="#8d9298"/>
        </linearGradient>
      </defs>
      <polygon points="0,0 620,0 593,35 0,35" fill="url(#band-gold)"/>
      <polygon points="620,0 632,0 605,35 593,35" fill="#000"/>
      <polygon points="632,0 700,0 700,35 605,35" fill="url(#band-silver)"/>
    </svg>
    <p class="web-address">WWW.<b>RENWICK-TOLLIVER</b>.CO.UK</p>
  </section>

  <section class="card card-back">
    <div class="back-brand"><span class="brand-square"></span>RENWICK TOLLIVER<br>CONSTRUCTION</div>
  </section>
</body>
</html>
```